Food and Beverage Business Cards

We need business cards with logo designs for a consultant in the food and beverage industry. We specialize in helping restaurants fix operational and management problems.
Specific areas of expertise include:
-Steps of service
-Staff management tools
-Standard operating procedures
-Profit and loss management
-Inventory
-Point of sales
-Bar Menu
-Mystery shopper service
-Handling and managing suppliers

Target Market(s)

Restaurant and bar owners and managers

Industry/Entity Type

Business

Contact Information for Business Card

Mathieu Girardot
Q&T Consulting
phone: 15027390614
mathqt@sampleinbox.com

Font styles to use
Other font styles liked:
• Check out the screen shot font idea

Colors

Designer to choose colors to be used in the design.

Requirements
Must have
• Must include QR code (See attachment)
• Logo should reflect our specific focus on the drinks side of the industry.
• Areas of Expertise:
• -Service Steps
• -Staff management tools
• -S.O.P
• -P&L Management
• -Inventory
• -P.O.S
• -Bar Menu
• -Mystery Shopper Service
• -Handling and Managing Suppliers

```html
<!DOCTYPE html>
<html lang="en">
<head>
<meta charset="utf-8">
<title>Q&amp;T Consulting Business Cards</title>
<link href="https://fonts.googleapis.com/css2?family=Roboto:wght@400;700&family=Roboto+Condensed:wght@400;700&display=swap" rel="stylesheet">
<style>
  :root {
    --bg: #e9e6e1;
    --card-white: #fbfbfb;
    --card-black: #111111;
    --band-grey: #5d5d5d;
    --band-edge: #3a3a3a;
    --ink-dark: #2a2a2a;
    --ink-light: #ffffff;
    --ink-soft: #e4e4e4;
    --badge: #d9d9d9;
  }
  * { margin: 0; padding: 0; box-sizing: border-box; }
  html, body { width: 1200px; height: 911px; overflow: hidden; }
  body {
    background: var(--bg);
    font-family: "Roboto", Arial, sans-serif;
    position: relative;
  }
  .card {
    position: absolute;
    top: 301px;
    width: 540px;
    height: 309px;
    border-radius: 22px;
    overflow: hidden;
    box-shadow: 0 10px 26px rgba(0,0,0,0.22);
  }
  .card--front { left: 40px; background: var(--card-white); }
  .card--back { left: 620px; background: var(--card-black); color: var(--ink-light); }

  .front-band { position: absolute; inset: 0; }
  .brand-name {
    font-family: "Roboto", Arial, sans-serif;
    font-weight: 700;
    white-space: nowrap;
  }
  .front-brand {
    position: absolute;
    left: 196px;
    top: 14px;
    font-size: 40px;
    line-height: 1.1;
    color: var(--ink-dark);
  }
  .contact {
    position: absolute;
    left: 30px;
    bottom: 22px;
    color: var(--ink-light);
    font-family: "Roboto Condensed", Arial, sans-serif;
  }
  .contact__name { font-size: 21px; font-weight: 700; letter-spacing: 0.3px; line-height: 1.2; }
  .contact__company { font-size: 15px; margin-top: 2px; letter-spacing: 0.4px; line-height: 1.2; }
  .contact__line {
    display: flex; align-items: center; gap: 8px;
    font-size: 15px; margin-top: 5px; line-height: 1.2;
  }
  .contact__line svg { width: 13px; height: 13px; flex: none; }
  .contact__lines { margin-top: 9px; }

  .back-brand {
    position: absolute;
    left: 0; right: 0;
    top: 48px;
    text-align: center;
    font-size: 50px;
    color: var(--ink-light);
  }
  .badges {
    position: absolute;
    right: 30px;
    top: 46px;
    display: flex;
    flex-direction: column;
    gap: 8px;
  }
  .badge { width: 34px; height: 34px; border-radius: 50%; background: var(--badge); }
  .badge--lead { width: 40px; height: 40px; }
  .expertise {
    position: absolute;
    left: 0; right: 0;
    top: 150px;
    text-align: center;
  }
  .expertise__title { font-size: 17px; font-weight: 700; margin-bottom: 12px; }
  .expertise__list { list-style: none; font-size: 13px; line-height: 1.55; color: var(--ink-soft); }
</style>
</head>
<body>
  <section class="card card--front">
    <svg class="front-band" viewBox="0 0 540 309" width="540" height="309" aria-hidden="true">
      <path d="M0 309 L0 166 C120 148 180 98 300 83 C400 70 470 58 540 46 L540 309 Z" fill="var(--band-edge)"/>
      <path d="M0 309 L0 171 C120 153 180 103 300 88 C400 75 470 63 540 51 L540 309 Z" fill="#ffffff"/>
      <path d="M0 309 L0 176 C120 158 180 108 300 93 C400 80 470 68 540 56 L540 309 Z" fill="var(--band-grey)"/>
    </svg>
    <div class="brand-name front-brand">Q&amp;T Harbor</div>
    <div class="contact">
      <div class="contact__name">MATHIEU GIRARDOT</div>
      <div class="contact__company">Q&amp;T CONSULTING</div>
      <div class="contact__lines">
        <div class="contact__line">
          <svg viewBox="0 0 24 24"><path fill="#fff" d="M6.6 10.8a15.2 15.2 0 0 0 6.6 6.6l2.2-2.2c.3-.3.7-.4 1-.2 1.1.4 2.3.6 3.6.6.6 0 1 .4 1 1V20c0 .6-.4 1-1 1A17 17 0 0 1 3 4c0-.6.4-1 1-1h3.5c.6 0 1 .4 1 1 0 1.3.2 2.5.6 3.6.1.3 0 .7-.2 1z"/></svg>
          <span>15027390614</span>
        </div>
        <div class="contact__line">
          <svg viewBox="0 0 24 24"><rect x="2" y="5" width="20" height="14" rx="1.5" fill="#fff"/><path d="M3 6l9 7 9-7" fill="none" stroke="#5d5d5d" stroke-width="2"/></svg>
          <span>mathqt@sampleinbox.com</span>
        </div>
      </div>
    </div>
  </section>

  <section class="card card--back">
    <div class="brand-name back-brand">Q&amp;T Harbor</div>
    <div class="badges" aria-hidden="true">
      <div class="badge badge--lead"></div>
      <div class="badge"></div>
      <div class="badge"></div>
    </div>
    <div class="expertise">
      <h2 class="expertise__title">Areas of Expertise</h2>
      <ul class="expertise__list">
        <li>Service Steps | Staff management tools | S.O.P | P&amp;L Management</li>
        <li>Inventory | P.O.S | Bar Menu | Mystery Shopper Service</li>
        <li>Handling and Managing Suppliers</li>
      </ul>
    </div>
  </section>
</body>
</html>
```